Design for a real estate wev portal

Contents and features of the site
---------------------------------
Website in 5 languages: French, Dutch, English, German, Spanish.
English name of the site: Harbor Nest Place
Main purpose of the site:
- allow people to rent their house/ appartment for flatsharing purposes.
- help people wanting to find a room in flatsharing
- help people to find additional roommates for their flatsharing
Key interaction sequence:
1. I create a "group" of people who have common interest/hobbies
2. People who have the same interests/hobbies join my group
3. I look for a house/appartment to host my group
Website structure will be the following:
- Home
- Groups
-- Look for a group
--- Join a group
-- Create a group
- Properties
-- Look for a house/appartement
-- Apply
- Sales conditions
- Contact
- My account
-- My profile
-- My groups OR my properties
Your mission
------------
The client has no graphical guidelines, simply a logo (see attached).
We need a (responsive compliant) design for the following pages (we expect PSD's from you. No HTML nor CSS):
1. homepage (see example and wireframe attached)
2. properties search result list (see wireframe attached)
3. "detailed" form for properties
4. groups search result list
5. "detailed" form for groups
6. my account page
FOR THE COMPETITION step we only expect from you the design of first 2 screens.
Based on that, we will select the designer who will win the project, and will have to design the 4 remaining screens.
Target Market(s)
B2C
Industry/Entity Type
Real Estate
Number of Pages Required
5+ page
Look and feel
Each slider illustrates characteristics of the customer's brand and the style your logo design should communicate.

```html
<!DOCTYPE html>
<html lang="en">
<head>
<meta charset="utf-8">
<title>Harbor Nest Place – Properties</title>
<link href="https://fonts.googleapis.com/css2?family=Open+Sans:wght@400;600;700&display=swap" rel="stylesheet">
<style>
:root{
  --green:#72bf44;
  --green-dark:#5ea635;
  --red:#f15a3f;
  --teal:#13929f;
  --ink:#333333;
  --muted:#666666;
  --line:#d6d6d6;
  --white:#ffffff;
  --hero-a:#0d2a2a;
  --hero-b:#23433e;
  --photo-blue:#3c5a8a;
  --photo-warm:#8a7a68;
  --photo-dusk:#2f4e80;
}
*{box-sizing:border-box;margin:0;padding:0}
html,body{width:1200px;height:2174px;overflow:hidden;background:var(--white)}
body{font-family:"Open Sans",Arial,sans-serif;color:var(--ink);position:relative}
.abs{position:absolute}

/* Hero */
.hero{left:0;top:0;width:1200px;height:432px;background:linear-gradient(160deg,var(--hero-b),var(--hero-a) 60%,#091c1e)}
.lang{left:991px;top:12px;width:77px;height:23px;background:#2a2a2a;color:#fff;font-size:14px;line-height:23px;padding-left:6px}
.lang::after{content:"";position:absolute;right:8px;top:7px;width:6px;height:6px;border-right:2px solid #fff;border-bottom:2px solid #fff;transform:rotate(45deg)}
.nav{left:129px;top:46px;width:942px;height:63px;background:var(--green);border-radius:4px}
.nav a{position:absolute;top:0;line-height:63px;color:#fff;font-size:16px;text-decoration:none}
.nav .active{left:0;width:75px;background:var(--green-dark);color:#1e3a10;text-align:center;border-radius:4px 0 0 4px}
.brand{left:482px;top:22px;width:215px;height:90px;background:#fff;border-radius:4px;display:flex;align-items:center;justify-content:center;gap:8px}
.brand span{font-size:21px;font-weight:600;color:var(--ink)}
.brand i{width:12px;height:12px;background:var(--green);display:block}
.hero-title{left:0;width:1200px;top:182px;text-align:center;color:#fff;font-size:38px;font-weight:400}
.hero-text{left:360px;width:480px;top:250px;text-align:center;color:#fff;font-size:14px;line-height:21px}
.hero-btn{left:478px;top:320px;width:254px;height:45px;border:1px solid var(--teal);color:#fff;font-size:18px;display:flex;align-items:center;justify-content:center;gap:8px}
.hero-btn b{color:#1aa3c4;font-size:26px;font-weight:400}

/* Social strip */
.social-strip{left:0;top:475px;width:22px}
.social-strip i{display:block;width:20px;height:20px;margin-bottom:2px;background:#2b7fb8}

/* Filters */
.field{height:41px;border:1px solid var(--line);font-size:14px;color:var(--muted);padding-left:8px;line-height:39px;background:#fff}
.field.select::after{content:"";position:absolute;right:12px;top:13px;width:8px;height:8px;border-right:2px solid #ccc;border-bottom:2px solid #ccc;transform:rotate(45deg)}
.sidebar .field{left:129px;width:220px}
.search-input{text-align:center;font-size:18px;color:#999}
.price-label{left:129px;top:842px;font-size:18px}
.track{left:129px;top:882px;width:220px;height:10px;background:#eee}
.track-fill{left:144px;top:884px;width:119px;height:6px;background:var(--green)}
.knob{top:881px;width:11px;height:11px;border-radius:50%;background:var(--teal)}
.scale{left:129px;top:896px;width:222px;display:flex;justify-content:space-between;font-size:12px}
.btn-search{left:129px;top:929px;width:220px;height:39px;background:var(--red);color:#fff;text-align:center;line-height:39px;font-size:18px}
.btn-bar{left:129px;top:991px;width:220px;height:39px;background:var(--green)}
.side-photo{left:130px;width:219px;height:143px;background:linear-gradient(180deg,var(--photo-blue),#2b3d5c)}
.side-title{left:129px;font-size:19px}
.side-btn{height:38px;border-radius:6px}
.side-btn.go{left:130px;width:100px;background:var(--green);display:flex;align-items:center;justify-content:center}
.side-btn.price{left:249px;width:100px;background:var(--red);color:#fff;text-align:center;line-height:38px;font-size:18px}

/* Results */
.results-head{left:369px;top:534px;font-size:24px;color:#555}
.results-count{right:154px;top:540px;font-size:14px}
.view-toggle{left:1000px;top:490px}
.listing{left:372px;width:680px;height:145px}
.listing .photo{position:absolute;left:0;top:0;width:218px;height:144px}
.listing h3{position:absolute;left:237px;top:-4px;font-size:19px;font-weight:400}
.listing .stars{position:absolute;right:0;top:-2px;font-size:14px;letter-spacing:1px}
.listing p{position:absolute;left:239px;top:36px;width:326px;font-size:14px;line-height:21px;text-align:justify;color:#444}
.listing .meta{position:absolute;left:237px;top:111px;display:flex;gap:18px;font-size:12px;font-weight:700;align-items:center}
.listing .meta span{display:flex;align-items:center;gap:4px}
.listing .go{position:absolute;left:586px;top:40px;width:88px;height:56px;background:var(--green);border-radius:6px;display:flex;align-items:center;justify-content:center}
.listing .price{position:absolute;left:586px;top:113px;width:88px;height:16px;background:var(--red);border-radius:8px;color:#fff;font-size:11px;font-weight:700;text-align:center;line-height:16px}
.ph-blue{background:linear-gradient(180deg,var(--photo-blue),#2b3d5c)}
.ph-mount{background:linear-gradient(180deg,#7aa0c8,#6f5a48)}
.ph-dusk{background:linear-gradient(180deg,var(--photo-dusk),#b49a62)}
.ph-room{background:linear-gradient(135deg,#d8d4cc,var(--photo-warm))}

.pager{left:638px;top:1720px;display:flex;gap:4px;font-size:13px}
.pager span{width:18px;height:18px;text-align:center;line-height:18px}
.pager .current{background:var(--green);color:#fff}

/* Footer */
.footer{left:0;top:1865px;width:1200px;height:309px;background:var(--teal);color:#fff}
.footer h4{position:absolute;font-size:24px;font-weight:400;top:52px}
.footer ul{position:absolute;list-style:none;top:104px;font-size:14px;line-height:25px}
.footer .mission{position:absolute;left:549px;top:112px;width:210px;font-size:14px;line-height:21px}
.footer .icons{position:absolute;left:822px;top:62px;display:flex;gap:5px}
.footer .icons i{width:20px;height:20px;background:#2a6fa8;display:block}
.footer .contact{position:absolute;left:824px;top:89px;font-size:14px;line-height:21px}
.footer .contact div{display:flex;align-items:center;gap:10px}
.footer .lang-foot{position:absolute;left:823px;top:168px;width:78px;height:22px;background:#1d7fa0;font-size:14px;line-height:22px;padding-left:6px}
</style>
</head>
<body>

<section class="abs hero" role="img" aria-label="Photo of a modern living room at night"></section>
<div class="abs lang">English</div>
<nav class="abs nav">
  <a class="active" href="#">Home</a>
  <a href="#" style="left:84px">Groups</a>
  <a href="#" style="left:159px">Properties</a>
  <a href="#" style="left:257px">My account</a>
  <a href="#" style="left:586px">Contact</a>
  <a href="#" style="left:665px">Sales conditions</a>
  <a href="#" style="left:807px">login</a>
  <a href="#" style="left:864px">Register</a>
</nav>
<div class="abs brand"><i></i><span>Harbor Nest Place</span></div>
<h1 class="abs hero-title">Harbor Nest Place</h1>
<p class="abs hero-text">It is a long established fact that a reader will be distracted by the readable content of a page when looking at its layout. The point of using</p>
<div class="abs hero-btn"><b>+</b>Add Your House</div>

<div class="abs social-strip"><i></i><i></i><i></i><i></i><i></i><i></i><i></i><i></i></div>

<aside class="sidebar">
  <div class="abs field search-input" style="top:480px">Location or Name</div>
  <div class="abs field select" style="top:540px">10 Rooms</div>
  <div class="abs field select" style="top:603px">Egypt</div>
  <div class="abs field select" style="top:664px">Cairo</div>
  <div class="abs field select" style="top:726px">Rent</div>
  <div class="abs field select" style="top:788px">Villa</div>
  <div class="abs price-label">Price</div>
  <div class="abs track"></div>
  <div class="abs track-fill"></div>
  <div class="abs knob" style="left:139px"></div>
  <div class="abs knob" style="left:257px"></div>
  <div class="abs scale"><span>10000</span><span>100000</span><span>1000000</span><span>10000000</span></div>
  <div class="abs btn-search">Search</div>
  <div class="abs btn-bar"></div>

  <div class="abs side-photo" style="top:1055px" role="img" aria-label="Photo of a lit house entrance"></div>
  <div class="abs side-title" style="top:1212px">House Ciro , Egypt</div>
  <div class="abs side-btn go" style="top:1252px"><svg width="30" height="26" viewBox="0 0 30 26" fill="none" stroke="#fff" stroke-width="2"><rect x="3" y="5" width="22" height="18"/><line x1="3" y1="11" x2="25" y2="11"/><line x1="9" y1="2" x2="9" y2="7"/><line x1="19" y1="2" x2="19" y2="7"/></svg></div>
  <div class="abs side-btn price" style="top:1252px">100$</div>

  <div class="abs side-photo" style="top:1311px" role="img" aria-label="Photo of a lit house entrance"></div>
  <div class="abs side-title" style="top:1468px">House Ciro , Egypt</div>
  <div class="abs side-btn go" style="top:1510px"><svg width="30" height="26" viewBox="0 0 30 26" fill="none" stroke="#fff" stroke-width="2"><rect x="3" y="5" width="22" height="18"/><line x1="3" y1="11" x2="25" y2="11"/><line x1="9" y1="2" x2="9" y2="7"/><line x1="19" y1="2" x2="19" y2="7"/></svg></div>
  <div class="abs side-btn price" style="top:1510px">100$</div>

  <div class="abs side-photo" style="top:1568px" role="img" aria-label="Photo of a lit house entrance"></div>
  <div class="abs side-title" style="top:1725px">House Ciro , Egypt</div>
  <div class="abs side-btn go" style="top:1766px"><svg width="30" height="26" viewBox="0 0 30 26" fill="none" stroke="#fff" stroke-width="2"><rect x="3" y="5" width="22" height="18"/><line x1="3" y1="11" x2="25" y2="11"/><line x1="9" y1="2" x2="9" y2="7"/><line x1="19" y1="2" x2="19" y2="7"/></svg></div>
  <div class="abs side-btn price" style="top:1766px">100$</div>
</aside>

<main>
  <div class="abs field select" style="left:369px;top:480px;width:141px;font-size:13px;color:#333">100 per page</div>
  <div class="abs field select" style="left:535px;top:480px;width:140px;font-size:13px;color:#333">Order By Rate</div>
  <svg class="abs view-toggle" width="51" height="22" viewBox="0 0 51 22" fill="#444">
    <rect x="0" y="1" width="4" height="4"/><rect x="6" y="1" width="18" height="4"/>
    <rect x="0" y="9" width="4" height="4"/><rect x="6" y="9" width="18" height="4"/>
    <rect x="0" y="17" width="4" height="4"/><rect x="6" y="17" width="18" height="4"/>
    <rect x="29" y="0" width="10" height="10"/><rect x="41" y="0" width="10" height="10"/>
    <rect x="29" y="12" width="10" height="10"/><rect x="41" y="12" width="10" height="10"/>
  </svg>
  <h2 class="abs results-head" style="font-weight:400">We found 30 Result</h2>
  <div class="abs results-count">you show 10 of 30 page 1</div>

  <!-- listing template repeated -->
  <article class="abs listing" style="top:578px">
    <div class="photo ph-blue" role="img" aria-label="Photo of a lit house entrance"></div>
    <h3>House Ciro , Egypt</h3><div class="stars">★★★★★★★</div>
    <p>It is a long established fact that a reader will be distracted by the readable content of a page when looking at its layout. The point of using</p>
    <div class="meta"><span><svg width="22" height="14" viewBox="0 0 22 14" fill="#555"><rect x="0" y="6" width="22" height="5"/><rect x="3" y="2" width="7" height="4"/><rect x="0" y="11" width="2" height="3"/><rect x="20" y="11" width="2" height="3"/></svg>: 5</span><span><svg width="18" height="14" viewBox="0 0 18 14" fill="#555"><rect x="0" y="7" width="18" height="4"/><rect x="13" y="0" width="3" height="7"/></svg>: 2</span><span><svg width="22" height="14" viewBox="0 0 22 14" fill="none" stroke="#555" stroke-width="1.6"><ellipse cx="11" cy="7" rx="10" ry="6"/><circle cx="11" cy="7" r="3"/></svg>: 50000</span><span><svg width="16" height="14" viewBox="0 0 16 14" fill="#555"><path d="M0 0h16v10H6l-4 4v-4H0z"/></svg>: 50000</span></div>
    <div class="go"><svg width="36" height="32" viewBox="0 0 30 26" fill="none" stroke="#fff" stroke-width="2"><rect x="3" y="5" width="22" height="18"/><line x1="3" y1="11" x2="25" y2="11"/><line x1="9" y1="2" x2="9" y2="7"/><line x1="19" y1="2" x2="19" y2="7"/></svg></div>
    <div class="price">100$</div>
  </article>

  <article class="abs listing" style="top:742px">
    <div class="photo ph-mount" role="img" aria-label="Photo of a mountain chalet"></div>
    <h3>House Ciro , Egypt</h3><div class="stars">★★★★★★★</div>
    <p>It is a long established fact that a reader will be distracted by the readable content of a page when looking at its layout. The point of using</p>
    <div class="meta"><span><svg width="22" height="14" viewBox="0 0 22 14" fill="#555"><rect x="0" y="6" width="22" height="5"/><rect x="3" y="2" width="7" height="4"/><rect x="0" y="11" width="2" height="3"/><rect x="20" y="11" width="2" height="3"/></svg>: 5</span><span><svg width="18" height="14" viewBox="0 0 18 14" fill="#555"><rect x="0" y="7" width="18" height="4"/><rect x="13" y="0" width="3" height="7"/></svg>: 2</span><span><svg width="22" height="14" viewBox="0 0 22 14" fill="none" stroke="#555" stroke-width="1.6"><ellipse cx="11" cy="7" rx="10" ry="6"/><circle cx="11" cy="7" r="3"/></svg>: 50000</span><span><svg width="16" height="14" viewBox="0 0 16 14" fill="#555"><path d="M0 0h16v10H6l-4 4v-4H0z"/></svg>: 50000</span></div>
    <div class="go"><svg width="36" height="32" viewBox="0 0 30 26" fill="none" stroke="#fff" stroke-width="2"><rect x="3" y="5" width="22" height="18"/><line x1="3" y1="11" x2="25" y2="11"/><line x1="9" y1="2" x2="9" y2="7"/><line x1="19" y1="2" x2="19" y2="7"/></svg></div>
    <div class="price">100$</div>
  </article>

  <article class="abs listing" style="top:906px">
    <div class="photo ph-dusk" role="img" aria-label="Photo of a modern house at dusk"></div>
    <h3>House Ciro , Egypt</h3><div class="stars">★★★★★★★</div>
    <p>It is a long established fact that a reader will be distracted by the readable content of a page when looking at its layout. The point of using</p>
    <div class="meta"><span><svg width="22" height="14" viewBox="0 0 22 14" fill="#555"><rect x="0" y="6" width="22" height="5"/><rect x="3" y="2" width="7" height="4"/><rect x="0" y="11" width="2" height="3"/><rect x="20" y="11" width="2" height="3"/></svg>: 5</span><span><svg width="18" height="14" viewBox="0 0 18 14" fill="#555"><rect x="0" y="7" width="18" height="4"/><rect x="13" y="0" width="3" height="7"/></svg>: 2</span><span><svg width="22" height="14" viewBox="0 0 22 14" fill="none" stroke="#555" stroke-width="1.6"><ellipse cx="11" cy="7" rx="10" ry="6"/><circle cx="11" cy="7" r="3"/></svg>: 50000</span><span><svg width="16" height="14" viewBox="0 0 16 14" fill="#555"><path d="M0 0h16v10H6l-4 4v-4H0z"/></svg>: 50000</span></div>
    <div class="go"><svg width="36" height="32" viewBox="0 0 30 26" fill="none" stroke="#fff" stroke-width="2"><rect x="3" y="5" width="22" height="18"/><line x1="3" y1="11" x2="25" y2="11"/><line x1="9" y1="2" x2="9" y2="7"/><line x1="19" y1="2" x2="19" y2="7"/></svg></div>
    <div class="price">100$</div>
  </article>

  <article class="abs listing" style="top:1070px">
    <div class="photo ph-room" role="img" aria-label="Photo of a living room interior"></div>
    <h3>House Ciro , Egypt</h3><div class="stars">★★★★★★★</div>
    <p>It is a long established fact that a reader will be distracted by the readable content of a page when looking at its layout. The point of using</p>
    <div class="meta"><span><svg width="22" height="14" viewBox="0 0 22 14" fill="#555"><rect x="0" y="6" width="22" height="5"/><rect x="3" y="2" width="7" height="4"/><rect x="0" y="11" width="2" height="3"/><rect x="20" y="11" width="2" height="3"/></svg>: 5</span><span><svg width="18" height="14" viewBox="0 0 18 14" fill="#555"><rect x="0" y="7" width="18" height="4"/><rect x="13" y="0" width="3" height="7"/></svg>: 2</span><span><svg width="22" height="14" viewBox="0 0 22 14" fill="none" stroke="#555" stroke-width="1.6"><ellipse cx="11" cy="7" rx="10" ry="6"/><circle cx="11" cy="7" r="3"/></svg>: 50000</span><span><svg width="16" height="14" viewBox="0 0 16 14" fill="#555"><path d="M0 0h16v10H6l-4 4v-4H0z"/></svg>: 50000</span></div>
    <div class="go"><svg width="36" height="32" viewBox="0 0 30 26" fill="none" stroke="#fff" stroke-width="2"><rect x="3" y="5" width="22" height="18"/><line x1="3" y1="11" x2="25" y2="11"/><line x1="9" y1="2" x2="9" y2="7"/><line x1="19" y1="2" x2="19" y2="7"/></svg></div>
    <div class="price">100$</div>
  </article>

  <article class="abs listing" style="top:1233px">
    <div class="photo ph-dusk" role="img" aria-label="Photo of a modern house at dusk"></div>
    <h3>House Ciro , Egypt</h3><div class="stars">★★★★★★★</div>
    <p>It is a long established fact that a reader will be distracted by the readable content of a page when looking at its layout. The point of using</p>
    <div class="meta"><span><svg width="22" height="14" viewBox="0 0 22 14" fill="#555"><rect x="0" y="6" width="22" height="5"/><rect x="3" y="2" width="7" height="4"/><rect x="0" y="11" width="2" height="3"/><rect x="20" y="11" width="2" height="3"/></svg>: 5</span><span><svg width="18" height="14" viewBox="0 0 18 14" fill="#555"><rect x="0" y="7" width="18" height="4"/><rect x="13" y="0" width="3" height="7"/></svg>: 2</span><span><svg width="22" height="14" viewBox="0 0 22 14" fill="none" stroke="#555" stroke-width="1.6"><ellipse cx="11" cy="7" rx="10" ry="6"/><circle cx="11" cy="7" r="3"/></svg>: 50000</span><span><svg width="16" height="14" viewBox="0 0 16 14" fill="#555"><path d="M0 0h16v10H6l-4 4v-4H0z"/></svg>: 50000</span></div>
    <div class="go"><svg width="36" height="32" viewBox="0 0 30 26" fill="none" stroke="#fff" stroke-width="2"><rect x="3" y="5" width="22" height="18"/><line x1="3" y1="11" x2="25" y2="11"/><line x1="9" y1="2" x2="9" y2="7"/><line x1="19" y1="2" x2="19" y2="7"/></svg></div>
    <div class="price">100$</div>
  </article>

  <article class="abs listing" style="top:1397px">
    <div class="photo ph-room" role="img" aria-label="Photo of a living room interior"></div>
    <h3>House Ciro , Egypt</h3><div class="stars">★★★★★★★</div>
    <p>It is a long established fact that a reader will be distracted by the readable content of a page when looking at its layout. The point of using</p>
    <div class="meta"><span><svg width="22" height="14" viewBox="0 0 22 14" fill="#555"><rect x="0" y="6" width="22" height="5"/><rect x="3" y="2" width="7" height="4"/><rect x="0" y="11" width="2" height="3"/><rect x="20" y="11" width="2" height="3"/></svg>: 5</span><span><svg width="18" height="14" viewBox="0 0 18 14" fill="#555"><rect x="0" y="7" width="18" height="4"/><rect x="13" y="0" width="3" height="7"/></svg>: 2</span><span><svg width="22" height="14" viewBox="0 0 22 14" fill="none" stroke="#555" stroke-width="1.6"><ellipse cx="11" cy="7" rx="10" ry="6"/><circle cx="11" cy="7" r="3"/></svg>: 50000</span><span><svg width="16" height="14" viewBox="0 0 16 14" fill="#555"><path d="M0 0h16v10H6l-4 4v-4H0z"/></svg>: 50000</span></div>
    <div class="go"><svg width="36" height="32" viewBox="0 0 30 26" fill="none" stroke="#fff" stroke-width="2"><rect x="3" y="5" width="22" height="18"/><line x1="3" y1="11" x2="25" y2="11"/><line x1="9" y1="2" x2="9" y2="7"/><line x1="19" y1="2" x2="19" y2="7"/></svg></div>
    <div class="price">100$</div>
  </article>

  <article class="abs listing" style="top:1561px">
    <div class="photo ph-room" role="img" aria-label="Photo of a living room interior"></div>
    <h3>House Ciro , Egypt</h3><div class="stars">★★★★★★★</div>
    <p>It is a long established fact that a reader will be distracted by the readable content of a page when looking at its layout. The point of using</p>
    <div class="meta"><span><svg width="22" height="14" viewBox="0 0 22 14" fill="#555"><rect x="0" y="6" width="22" height="5"/><rect x="3" y="2" width="7" height="4"/><rect x="0" y="11" width="2" height="3"/><rect x="20" y="11" width="2" height="3"/></svg>: 5</span><span><svg width="18" height="14" viewBox="0 0 18 14" fill="#555"><rect x="0" y="7" width="18" height="4"/><rect x="13" y="0" width="3" height="7"/></svg>: 2</span><span><svg width="22" height="14" viewBox="0 0 22 14" fill="none" stroke="#555" stroke-width="1.6"><ellipse cx="11" cy="7" rx="10" ry="6"/><circle cx="11" cy="7" r="3"/></svg>: 50000</span><span><svg width="16" height="14" viewBox="0 0 16 14" fill="#555"><path d="M0 0h16v10H6l-4 4v-4H0z"/></svg>: 50000</span></div>
    <div class="go"><svg width="36" height="32" viewBox="0 0 30 26" fill="none" stroke="#fff" stroke-width="2"><rect x="3" y="5" width="22" height="18"/><line x1="3" y1="11" x2="25" y2="11"/><line x1="9" y1="2" x2="9" y2="7"/><line x1="19" y1="2" x2="19" y2="7"/></svg></div>
    <div class="price">100$</div>
  </article>

  <nav class="abs pager"><span>‹</span><span>1</span><span>2</span><span class="current">3</span><span>4</span><span>5</span><span>›</span></nav>
</main>

<footer class="abs footer">
  <h4 style="left:129px">Links</h4>
  <ul style="left:130px"><li>Home</li><li>Groups</li><li>Sales conditions</li><li>Contact</li><li>My account</li><li>Login</li></ul>
  <ul style="left:288px"><li>Join a group</li><li>Create a group</li><li>Look for a house/appartement</li><li>My profile</li><li>My account</li><li>My groups OR my properties</li></ul>
  <h4 style="left:548px">Our mission</h4>
  <p class="mission">It is a long established fact that a reader will be distracted by the readable content of a page when looking at its layout. The point of using Lorem Ipsum is that it has a more-or-less</p>
  <div class="icons"><i></i><i></i><i></i><i></i><i></i><i></i><i></i><i></i><i></i></div>
  <div class="contact">
    <div><svg width="16" height="11" viewBox="0 0 16 11" fill="#fff"><path d="M0 0h16v11H0z"/><path d="M0 0l8 6 8-6" fill="none" stroke="#13929f" stroke-width="1.5"/></svg>hello@harbornestplace.com</div>
    <div><svg width="16" height="11" viewBox="0 0 16 11" fill="#fff"><path d="M0 0h16v11H0z"/><path d="M0 0l8 6 8-6" fill="none" stroke="#13929f" stroke-width="1.5"/></svg>hello@harbornestplace.com</div>
    <div style="margin-top:4px">copy rihgt 2017</div>
  </div>
  <div class="lang-foot">English ⌄</div>
</footer>

</body>
</html>
```